Hong Kong based International Remittance and ForEx company requires website design

We need a website designed for a new European - Hong Kong based ForEx & fund remittence entity.

The company specialises in larger corporate & high net worth private client trades, therefore the design must aesthetically reflect this (sophisticated). As a theme colour, financial entities tend to use either blue or red; if blue, our preference is a darker blue. Visually, our preference is less copy, more imagery.

Number of pages would be limited; landing (home), about us, client registration (x1 Corporate form, x1 Private Client form), Contact Us.

Have uploaded the existing logo - please note this is to be redesigned, although the colour scheme will remain the same. Please also note that copy will follow - please use Lorem Ipsum.

Target Market(s)

Medium to large Corporations. High net worth individuals.

Industry/Entity Type

Financial Service

Coding

Coded - Design and coding required

Number of Pages Required

4 page

Font styles to use
Serif

Requirements
Nice to have
• ForEx ticker,

```html
<!DOCTYPE html>
<html lang="en">
<head>
<meta charset="utf-8">
<title>Harbourline Capital – Home</title>
<link rel="stylesheet" href="https://fonts.googleapis.com/css2?family=Rufina:wght@400;700&family=Open+Sans:ital,wght@0,400;0,600;0,700;1,400&display=swap">
<style>
:root{
  --red:#c8161d;
  --navy:#0c4c8a;
  --ink:#333;
  --footer:#1d2631;
  --footer-dark:#161d26;
  --ticker:#111;
  --serif:'Rufina',Georgia,serif;
  --sans:'Open Sans',Arial,sans-serif;
}
*{margin:0;padding:0;box-sizing:border-box}
html,body{width:796px;height:1200px;overflow:hidden;background:#fff}
body{position:relative;font-family:var(--sans);color:var(--ink)}
.abs{position:absolute}

/* header */
.topline{left:0;top:0;width:796px;height:2px;background:var(--red)}
.header{left:0;top:2px;width:796px;height:62px;background:#fff}
.nav-item{top:24px;font-family:var(--serif);font-size:10.5px;color:#333;white-space:nowrap}
.nav-item.active{color:var(--red)}
.nav-search{left:619px;top:27px}
.lang{left:646px;top:24px;display:flex;align-items:center;gap:6px;font-size:8.5px;color:#888;letter-spacing:.3px}

/* brand */
.brand{left:58px;top:22px;width:120px;height:84px;border-radius:0 0 60px 60px;background:#fff;z-index:3;display:flex;flex-direction:column;align-items:center}
.brand-dot{width:46px;height:46px;border-radius:50%;background:var(--red);margin-top:-14px}
.brand-name{font-family:var(--serif);font-size:13px;color:#333;margin-top:5px;letter-spacing:.5px}

/* hero */
.hero{left:0;top:64px;width:796px;height:284px;background:linear-gradient(180deg,#7fa7c6 0%,#5d88a8 45%,#3d8a9a 75%,#2f7a86 100%)}
.hero-title{left:63px;top:146px;font-family:var(--serif);font-weight:700;font-size:35px;color:#fff}
.hero-sub{left:65px;top:198px;width:380px;font-style:italic;font-size:11.2px;line-height:19px;color:#fff}
.btn{display:inline-block;background:var(--red);color:#fff;font-weight:700;text-transform:uppercase}
.hero-btn{left:66px;top:250px;width:98px;height:30px;border:2px solid #fff;font-size:9.5px;text-align:center;line-height:26px}
.dots{left:373px;top:308px;display:flex;gap:2px}
.dots span{width:11px;height:11px;border:1.5px solid #fff;border-radius:50%}
.dots .on{background:var(--navy)}

/* ticker */
.ticker{left:0;top:348px;width:796px;height:30px;background:var(--ticker);color:#fff;font-size:10.5px;line-height:30px}
.ticker-arrow{top:0;width:34px;height:30px;background:#000;display:flex;align-items:center;justify-content:center}
.ticker-track{left:51px;top:0;white-space:nowrap}
.up{color:#7cc142}.down{color:#e0262c}

/* welcome */
.welcome-title{left:65px;top:404px;font-family:var(--serif);font-weight:700;font-size:15px;color:#333}
.welcome-img{left:66px;top:442px;width:174px;height:139px;border:2px solid #ddd;background:linear-gradient(135deg,#1d3550,#3f6d93 55%,#1a2f47)}
.welcome-text{left:258px;top:438px;width:190px;font-size:8px;line-height:14.8px;color:#555}
.welcome-btn{left:258px;top:554px;width:81px;height:28px;font-size:8.5px;text-align:center;line-height:28px;border-radius:2px}

/* converter */
.string{top:378px;width:2px;height:64px;background:#e6d5dc}
.knob{width:12px;height:12px;border-radius:50%;background:#fff;border:2px solid #c9d8ea}
.converter{left:470px;top:430px;width:260px;height:152px;background:var(--navy);border:3px solid #fff;outline:1px solid #ddd}
.field{height:25px;background:#fff;font-size:8.5px;color:#555;line-height:25px;padding-left:7px}
.select{display:flex;justify-content:space-between}
.select i{width:28px;background:#ccc;display:flex;align-items:center;justify-content:center}
.result{color:#fff;font-size:8.5px}
.result b{font-size:11px}

/* expertise */
.expertise{left:0;top:616px;width:796px;height:245px;background:linear-gradient(90deg,#1f4f86 0%,#2d4b80 50%,#4a3d70 100%)}
.exp-title{left:0;top:640px;width:796px;text-align:center;font-family:var(--serif);font-weight:700;font-size:15.5px;color:#fff}
.exp-item{top:685px;width:190px;text-align:center;color:#fff}
.exp-icon{width:74px;height:74px;margin:0 auto;border-radius:50%;background:var(--red);border:3px solid #fff;display:flex;align-items:center;justify-content:center}
.exp-item h3{font-family:var(--serif);font-size:11.5px;margin-top:10px}
.exp-item p{font-size:8px;line-height:14.4px;color:#d8deea;margin-top:6px}

/* testimonial */
.quote-bg{left:92px;top:896px;width:60px;height:60px;border-radius:50%;background:#e5e5e5;font-family:var(--serif);font-size:56px;color:#c9c9c9;text-align:center;line-height:84px}
.avatar{left:137px;top:889px;width:74px;height:74px;border-radius:50%;background:linear-gradient(160deg,#d9d9d9,#8d8d8d 60%,#3a3a3a)}
.quote{left:233px;top:892px;width:470px;font-style:italic;font-size:8.4px;line-height:18px;color:#666}
.author{left:233px;top:953px;font-family:var(--serif);font-weight:700;font-size:10.5px;color:var(--red)}
.t-arrow{top:918px;color:#bbb;font-size:18px}

/* footer */
.footer{left:0;top:998px;width:796px;height:154px;background:var(--footer)}
.badge{left:100px;top:1020px;width:92px;height:116px;border-radius:46px 46px 20px 20px;background:linear-gradient(180deg,#d7a93c,#a9802a)}
.f-col{top:1018px;color:#fff}
.f-col h4{font-family:var(--serif);font-weight:700;font-size:12px;margin-bottom:14px}
.f-col li{list-style:none;font-size:8px;line-height:17px;color:#e6e6e6}
.f-col p{font-size:8px;line-height:13.6px;color:#e6e6e6}
.f-input{width:174px;height:22px;background:#fff;color:#888;font-size:8px;line-height:22px;padding-left:10px;margin-top:8px}
.f-btn{margin-top:9px;width:66px;height:23px;border:1px solid #fff;font-size:8.5px;text-align:center;line-height:21px;border-radius:2px}
.c-row{display:flex;gap:10px;font-size:8px;line-height:11px;color:#e6e6e6;margin-bottom:8px}
.c-row svg{flex:none;margin-top:1px}
.bottom{left:0;top:1152px;width:796px;height:48px;background:var(--footer-dark);border-top:1px solid #2b3440}
.copy{left:66px;top:1170px;font-size:8px;color:#ddd}
.social{top:1164px;width:24px;height:24px;border:1.5px solid #fff;border-radius:50%}
</style>
</head>
<body>

<div class="abs header"></div>
<div class="abs topline"></div>

<div class="abs brand"><div class="brand-dot"></div><div class="brand-name">HARBOURLINE</div></div>

<nav>
  <span class="abs nav-item active" style="left:205px">Home</span>
  <span class="abs nav-item" style="left:252px">About Us</span>
  <span class="abs nav-item" style="left:315px">International Payments</span>
  <span class="abs nav-item" style="left:445px">Client Application</span>
  <span class="abs nav-item" style="left:549px">Contact Us</span>
</nav>
<svg class="abs nav-search" width="9" height="9" viewBox="0 0 10 10"><circle cx="4" cy="4" r="3" fill="none" stroke="#333" stroke-width="1.6"/><line x1="6.3" y1="6.3" x2="9.2" y2="9.2" stroke="#333" stroke-width="1.6"/></svg>
<div class="abs lang">
  <svg width="24" height="12" viewBox="0 0 24 12"><circle cx="6" cy="6" r="5" fill="none" stroke="#c8161d" stroke-width="1.3"/><path d="M1 6h10M6 1c-2.5 3-2.5 7 0 10M6 1c2.5 3 2.5 7 0 10" fill="none" stroke="#c8161d" stroke-width="1"/></svg>
  LANGUAGE
</div>

<section class="abs hero" role="img" aria-label="Photo of the harbour skyline with a red-sailed junk boat on the water"></section>
<h1 class="abs hero-title">Harbourline Capital</h1>
<p class="abs hero-sub">We are a new ForEx &amp; fund remittance entity based in European. We Excel in larger corporate &amp; high net worth private client trades.</p>
<a class="abs btn hero-btn">Get More Info</a>
<div class="abs dots"><span></span><span class="on"></span><span></span><span></span></div>

<div class="abs ticker">
  <div class="abs ticker-track">
    Nexa nxa 380.11 <span class="up">▲ 1.51 ▲ 0.50%</span> Nexa nxa 380.11 <span class="down">▼ 1.51 ▼ 0.50%</span> Orion Trade orn 380.11 <span class="up">▲ 1.51 ▲ 0.50%</span> Nexa nxa 380.11
  </div>
  <div class="abs ticker-arrow" style="left:0"><svg width="12" height="10" viewBox="0 0 12 10"><path d="M6 1 2 5l4 4M11 1 7 5l4 4" fill="none" stroke="#fff" stroke-width="1.6"/></svg></div>
  <div class="abs ticker-arrow" style="left:762px"><svg width="12" height="10" viewBox="0 0 12 10"><path d="M1 1l4 4-4 4M6 1l4 4-4 4" fill="none" stroke="#fff" stroke-width="1.6"/></svg></div>
</div>

<h2 class="abs welcome-title">Welcome to Harbourline</h2>
<div class="abs welcome-img" role="img" aria-label="Close-up photo of a currency exchange rate board"></div>
<p class="abs welcome-text">Harbourline Capital Limited is a regulated Money Service Operator Number (16-04-02918), licensed authorised by the Northbay Licensing Bureau.<br><br>We provide the international settlement and reconciliation of funds ..</p>
<a class="abs btn welcome-btn">Read More &gt;&gt;</a>

<div class="abs string" style="left:517px"></div>
<div class="abs string" style="left:681px"></div>
<div class="abs converter">
  <div class="abs field" style="left:11px;top:29px;width:70px">100</div>
  <div class="abs field select" style="left:89px;top:29px;width:154px">British Pound Sterling<i><svg width="8" height="5"><path d="M0 0h8L4 5z" fill="#666"/></svg></i></div>
  <div class="abs field" style="left:11px;top:63px;width:70px">1078.05</div>
  <div class="abs field select" style="left:89px;top:63px;width:154px">Hong Kong Dollar<i><svg width="8" height="5"><path d="M0 0h8L4 5z" fill="#666"/></svg></i></div>
  <div class="abs result" style="left:13px;top:106px"><b>100.00</b></div>
  <div class="abs result" style="left:97px;top:108px">British Pound Sterling is</div>
  <div class="abs result" style="left:13px;top:125px"><b>1,078.040</b></div>
  <div class="abs result" style="left:97px;top:127px">Hong Kong Dollar</div>
</div>
<div class="abs knob" style="left:512px;top:438px"></div>
<div class="abs knob" style="left:676px;top:438px"></div>

<section class="abs expertise" role="img" aria-label="Background photo of financial charts in blue and violet tones"></section>
<h2 class="abs exp-title">Our Expertise</h2>
<div class="abs exp-item" style="left:74px">
  <div class="exp-icon"><svg width="30" height="20" viewBox="0 0 30 20"><rect x="1" y="2" width="28" height="16" rx="1" fill="none" stroke="#fff" stroke-width="2.4"/><circle cx="15" cy="10" r="5" fill="#fff"/><rect x="14" y="7" width="2" height="6" fill="#c8161d"/></svg></div>
  <h3>International Money Transfer</h3>
  <p>Lorem ipsum dolor sit amet, consectetur adi pisi ng elit, sed do eiusmod tempor iunt ut labore et dolore magna aliqsmod</p>
</div>
<div class="abs exp-item" style="left:307px">
  <div class="exp-icon"><svg width="26" height="20" viewBox="0 0 26 20"><path d="M2 6h19M16 1l5 5-5 5M24 14H5M10 9l-5 5 5 5" fill="none" stroke="#fff" stroke-width="2.6"/></svg></div>
  <h3>Foreign Exchange</h3>
  <p>Lorem ipsum dolor sit amet, consectetur adi pisi ng elit, sed do eiusmod tempor iunt ut labore et dolore magna aliqsmod</p>
</div>
<div class="abs exp-item" style="left:542px">
  <div class="exp-icon"><svg width="28" height="24" viewBox="0 0 28 24"><rect x="1" y="1" width="26" height="17" rx="1" fill="#fff"/><rect x="4" y="4" width="20" height="11" fill="#c8161d"/><rect x="11" y="18" width="6" height="3" fill="#fff"/><rect x="7" y="21" width="14" height="2" fill="#fff"/></svg></div>
  <h3>Paying &amp; Receiving Agency</h3>
  <p>Lorem ipsum dolor sit amet, consectetur adi pisi ng elit, sed do eiusmod tempor iunt ut labore et dolore magna aliqsmod</p>
</div>

<div class="abs quote-bg">“</div>
<div class="abs avatar" role="img" aria-label="Portrait photo of the client giving the testimonial"></div>
<span class="abs t-arrow" style="left:64px">‹</span>
<span class="abs t-arrow" style="left:721px">›</span>
<p class="abs quote">It is a long established fact that a reader will be distracted by the readable content of a page when looking at its layout. The point of using Lorem Ipsum is that it has a more-or-less normal distribution of letters, as opposed to using 'Content here, content here', making it look like readable English.</p>
<div class="abs author">- Daniel Reeve</div>

<footer class="abs footer"></footer>
<div class="abs badge" role="img" aria-label="Licensing authority badge"></div>
<div class="abs f-col" style="left:254px">
  <h4>Information</h4>
  <ul><li>Home</li><li>About us</li><li>International Payments</li><li>Client Applications</li><li>Contact Us</li></ul>
</div>
<div class="abs f-col" style="left:378px">
  <h4>Newsletter</h4>
  <p>Register Your email address to get<br>information abiout us</p>
  <div class="f-input">Email Address</div>
  <div class="btn f-btn">Subscribe</div>
</div>
<div class="abs f-col" style="left:588px">
  <h4>Contact Us</h4>
  <div class="c-row"><svg width="7" height="10" viewBox="0 0 7 10"><path d="M3.5 0A3.5 3.5 0 0 0 0 3.5C0 6 3.5 10 3.5 10S7 6 7 3.5A3.5 3.5 0 0 0 3.5 0z" fill="#fff"/><circle cx="3.5" cy="3.5" r="1.3" fill="#1d2631"/></svg><span>212 Harbour View Rd, Suite 8,<br>Central 0410</span></div>
  <div class="c-row"><svg width="9" height="9" viewBox="0 0 10 10"><path d="M2 0l2 2.5-1.2 1.3a6 6 0 0 0 3.4 3.4L7.5 6 10 8l-1.5 2C4 10 0 6 0 1.5z" fill="#fff"/></svg><span>(852) 3100 4521</span></div>
  <div class="c-row"><svg width="10" height="9" viewBox="0 0 10 9"><rect x="0" y="2" width="10" height="7" rx="1" fill="#fff"/><rect x="2" y="0" width="6" height="3" fill="#fff"/><rect x="2" y="4" width="6" height="3" fill="#1d2631"/></svg><span>(852) 3100 4522</span></div>
  <div class="c-row"><svg width="10" height="8" viewBox="0 0 10 8"><rect width="10" height="8" fill="#fff"/><path d="M0 0l5 4 5-4" fill="none" stroke="#1d2631"/></svg><span>info@harbourlinecapital.example</span></div>
</div>

<div class="abs bottom"></div>
<p class="abs copy">Copyrights ©2016, Harbourline Capital. All rights reserved.</p>
<div class="abs social" style="left:621px" aria-label="Social link"></div>
<div class="abs social" style="left:649px" aria-label="Social link"></div>
<div class="abs social" style="left:678px" aria-label="Social link"></div>
<div class="abs social" style="left:706px" aria-label="Social link"></div>

</body>
</html>
```